Varnex Consulting Business card design.

See our website www.varnexconsulting.example which will give you a good idea of what we are about. The font is called 'Play'.

I'd like a standout business card in keeping with the themes and branding on the website

Target Market(s)

professionals. HR directors

Industry/Entity Type

Business

Contact Information for Business Card

Varnex Consulting PO Box 3172 Merrowdale NSW 2291 1300 485 193 Gavin Threlkeld Principal email: career@varnexconsulting.example ABN: 71203948865

Font styles to use
Other font styles liked:
• Play

Requirements
Must have
• Must have same design colours and branding as website.
• On back I'd prefer a list of the things we do which appears below the name at the header on the website

```html
<!DOCTYPE html>
<html lang="en">
<head>
<meta charset="utf-8">
<title>Varnex Consulting – Business Card</title>
<link rel="stylesheet" href="https://fonts.googleapis.com/css2?family=Play:wght@400;700&family=Arimo:wght@400;700&display=swap">
<style>
  :root {
    --page: #e9ebee;
    --navy: #0f2238;
    --navy-deep: #081626;
    --navy-light: #1d3650;
    --blue: #2a8fdc;
    --white: #ffffff;
    --paper-shade: #eef0f2;
    --ink-light: #d4dbe3;
    --ink-muted: #9aa7b5;
  }
  * { margin: 0; padding: 0; box-sizing: border-box; }
  html, body { width: 1200px; height: 950px; overflow: hidden; }
  body {
    background: var(--page);
    display: flex;
    flex-direction: column;
    align-items: center;
    justify-content: center;
    gap: 44px;
  }
  .card {
    position: relative;
    width: 660px;
    height: 403px;
    overflow: hidden;
    box-shadow: 0 10px 28px rgba(0, 0, 0, 0.22);
  }
  .card-art { position: absolute; inset: 0; width: 100%; height: 100%; }

  /* Back */
  .card--back {
    background: linear-gradient(120deg, var(--navy-deep) 0%, var(--navy) 55%, var(--navy-light) 100%);
  }
  .back-brand {
    position: absolute;
    right: 60px;
    top: 150px;
    text-align: right;
  }
  .back-brand .wordmark {
    font-family: 'Play', sans-serif;
    font-size: 38px;
    letter-spacing: 3px;
    color: var(--ink-light);
    text-transform: uppercase;
  }
  .services {
    margin-top: 22px;
    font-family: 'Arimo', sans-serif;
    font-size: 16px;
    letter-spacing: 0.5px;
    color: var(--ink-muted);
  }
  .services .divider { color: var(--blue); margin: 0 8px; }

  /* Front */
  .card--front { background: var(--white); }
  .front-brand {
    position: absolute;
    left: 44px;
    top: 40px;
    font-family: 'Play', sans-serif;
    font-size: 38px;
    letter-spacing: 3px;
    color: var(--navy);
    text-transform: uppercase;
  }
  .contact-list {
    position: absolute;
    left: 28px;
    top: 236px;
    list-style: none;
    font-family: 'Arimo', sans-serif;
    font-size: 17px;
    line-height: 1.45;
    color: var(--white);
  }
  .contact-list li { display: flex; align-items: center; gap: 9px; }
  .contact-list svg { width: 15px; height: 15px; flex: none; }
  .holder {
    position: absolute;
    right: 36px;
    top: 250px;
    text-align: right;
    font-family: 'Arimo', sans-serif;
  }
  .holder-name {
    font-size: 23px;
    font-weight: 700;
    color: var(--blue);
    letter-spacing: 0.3px;
  }
  .holder-role, .holder-address {
    font-size: 18px;
    color: var(--ink-light);
    line-height: 1.35;
  }
  .holder-role { margin-bottom: 4px; }
</style>
</head>
<body>

  <section class="card card--back" aria-label="Business card back">
    <div class="back-brand">
      <div class="wordmark">Varnex Consulting</div>
      <div class="services">Recruiting<span class="divider">|</span>Leadership<span class="divider">|</span>Outplacement</div>
    </div>
  </section>

  <section class="card card--front" aria-label="Business card front">
    <svg class="card-art" viewBox="0 0 660 403" aria-hidden="true">
      <defs>
        <linearGradient id="paper" x1="0" y1="0" x2="1" y2="1">
          <stop offset="0" stop-color="#ffffff"/>
          <stop offset="1" stop-color="#e6e9ec"/>
        </linearGradient>
        <linearGradient id="panel" x1="0" y1="0" x2="1" y2="0">
          <stop offset="0" stop-color="#0a1a2c"/>
          <stop offset="0.6" stop-color="#10253c"/>
          <stop offset="1" stop-color="#223a54"/>
        </linearGradient>
      </defs>
      <rect width="660" height="403" fill="url(#paper)"/>
      <polygon class="accent-band" points="0,156 262,156 279,174 0,174" fill="#2a8fdc"/>
      <polygon class="contact-panel" points="0,180 272,180 302,222 660,222 660,403 0,403" fill="url(#panel)"/>
    </svg>

    <div class="front-brand">Varnex Consulting</div>

    <ul class="contact-list">
      <li>
        <svg viewBox="0 0 16 16"><path fill="#ffffff" d="M2 5c0-2 2-3 6-3s6 1 6 3v1h-3V4.5C10 4 9 4 8 4s-2 0-3 .5V6H2zM4 7h8l2 6H2z"/><circle cx="8" cy="10" r="1.6" fill="#0f2238"/></svg>
        1300 485 193
      </li>
      <li>
        <svg viewBox="0 0 16 16"><rect x="1" y="3" width="14" height="10" fill="#ffffff"/><path d="M1 3l7 6 7-6" fill="none" stroke="#0f2238" stroke-width="1.4"/></svg>
        career@varnexconsulting.example
      </li>
      <li>
        <svg viewBox="0 0 16 16"><circle cx="8" cy="8" r="7" fill="#ffffff"/><path d="M1 8h14M8 1c-3 3-3 11 0 14M8 1c3 3 3 11 0 14" fill="none" stroke="#0f2238" stroke-width="1"/></svg>
        www.varnexconsulting.example
      </li>
    </ul>

    <div class="holder">
      <div class="holder-name">Gavin Threlkeld</div>
      <div class="holder-role">Principal</div>
      <div class="holder-address">PO Box 3172 Merrowdale<br>NSW 2291</div>
    </div>
  </section>

</body>
</html>
```